Bramblewood Card Company Business Cards

We are a trading card store with Glimmorax, sports and other TCG cards, we need a business card design that encompasses a clean cut, modern style with a retro flare. website is bramblewoodcardco.com for reference. Can utilize a comic book era feel or a more modern outdoor feel to utilize the "Pacific Northwest" elements of tress, mountains, etc.

Industry/Entity Type

Trading cards and collectibles

Contact Information for Business Card

business name, email address, phone number, name, owner job title

Font styles to use
Sans Serif

```html
<!DOCTYPE html>
<html lang="en">
<head>
<meta charset="utf-8">
<title>Bramblewood Card Company – Business Card</title>
<link href="https://fonts.googleapis.com/css2?family=Montserrat:wght@400;500;700;800&display=swap" rel="stylesheet">
<style>
  :root {
    --bg: #1f2023;
    --card-white: #ffffff;
    --brand-blue: #1eb6dc;
    --brand-blue-deep: #159fc4;
    --ink: #2b2b2e;
    --slate: #5e5f62;
    --rule: #b9bcc0;
  }
  * { box-sizing: border-box; margin: 0; padding: 0; }
  html, body { width: 1200px; height: 900px; overflow: hidden; background: var(--bg); }
  body { font-family: "Montserrat", sans-serif; position: relative; }

  .card {
    position: absolute;
    width: 560px; height: 320px;
    left: 320px;
    border-radius: 22px;
    overflow: hidden;
  }
  .card--front { top: 100px; background: var(--card-white); }
  .card--back  { top: 480px; background: var(--brand-blue); display: flex; align-items: center; justify-content: center; }

  .front-band { position: absolute; left: 0; bottom: 0; width: 560px; height: 22px; }

  .brand {
    position: absolute; left: 34px; top: 0; width: 190px; height: 298px;
    display: flex; flex-direction: column; align-items: center; justify-content: center; gap: 12px;
    text-align: center;
  }
  .brand-mark { width: 34px; height: 34px; background: var(--slate); }
  .brand-name {
    font-weight: 800; font-size: 21px; line-height: 1.15; letter-spacing: 0.5px;
    text-transform: uppercase; color: var(--slate);
  }

  .divider { position: absolute; left: 248px; top: 60px; width: 1.5px; height: 180px; background: var(--rule); }

  .details { position: absolute; left: 274px; top: 56px; color: var(--ink); }
  .person-name { font-weight: 700; font-size: 25px; letter-spacing: 1px; text-transform: uppercase; color: var(--brand-blue); }
  .person-role { font-size: 15px; margin-top: 2px; }
  .address { font-size: 15px; line-height: 1.4; margin-top: 14px; }
  .contacts { list-style: none; margin-top: 10px; font-size: 15px; line-height: 1.55; }
  .contacts li { display: flex; align-items: center; gap: 8px; }
  .contacts svg { width: 12px; height: 12px; flex: none; }

  .back-name {
    font-weight: 800; font-size: 30px; line-height: 1.15; letter-spacing: 1px;
    text-transform: uppercase; color: var(--card-white); text-align: center;
  }
</style>
</head>
<body>
  <section class="card card--front" aria-label="Business card front">
    <svg class="front-band" viewBox="0 0 560 22" aria-hidden="true">
      <polygon points="0,0 200,0 214,22 0,22" fill="var(--brand-blue)"/>
    </svg>

    <div class="brand">
      <span class="brand-mark"></span>
      <p class="brand-name">Bramblewood<br>Card Company</p>
    </div>

    <div class="divider"></div>

    <div class="details">
      <h1 class="person-name">Dorian Hale</h1>
      <p class="person-role">CEO/Founder</p>
      <p class="address">P.O. Box 3817 Street<br>Country Name CD 6021</p>
      <ul class="contacts">
        <li>
          <svg viewBox="0 0 12 12" aria-hidden="true"><path d="M2.5 1 L4.5 1 L5.3 3.6 L4 4.6 Q5 7 7.4 8 L8.4 6.7 L11 7.5 L11 9.5 Q10.5 11 9 11 Q1 10 1 2.5 Q1 1 2.5 1 Z" fill="var(--brand-blue)"/></svg>
          (555) 284 3190
        </li>
        <li>
          <svg viewBox="0 0 12 12" aria-hidden="true"><rect x="0.5" y="2" width="11" height="8" rx="1" fill="var(--brand-blue)"/><path d="M1 2.5 L6 6.5 L11 2.5" stroke="#fff" stroke-width="1" fill="none"/></svg>
          info@bramblewoodcardco.com
        </li>
        <li>
          <svg viewBox="0 0 12 12" aria-hidden="true"><circle cx="6" cy="6" r="5.5" fill="var(--brand-blue)"/><path d="M0.5 6 H11.5 M6 0.5 V11.5 M6 0.5 Q2.5 6 6 11.5 M6 0.5 Q9.5 6 6 11.5" stroke="#fff" stroke-width="0.8" fill="none"/></svg>
          www.bramblewoodcardco.com
        </li>
      </ul>
    </div>
  </section>

  <section class="card card--back" aria-label="Business card back">
    <p class="back-name">Bramblewood<br>Card Company</p>
  </section>
</body>
</html>
```